German Headhunter/ HR Consultancy needs Business Cards Design

We need a business Card Design for our Company in Stuttgart. We are specialized as Headhunter/ HR Consultancy in Placement of specialist and managers in permanent employment. Please refer to our business logo.

```html
<!DOCTYPE html>
<html lang="de">
<head>
<meta charset="utf-8">
<title>Kernwerk Personalberatung – Visitenkarten</title>
<link href="https://fonts.googleapis.com/css2?family=Roboto:wght@400;700&display=swap" rel="stylesheet">
<style>
  :root {
    --brand-blue: #3a54a8;
    --ink-grey: #8a8a8a;
    --rule-grey: #c4c4c4;
    --paper: #ffffff;
    --backdrop: #2b2b2b;
  }
  * { box-sizing: border-box; margin: 0; padding: 0; }
  html, body {
    width: 1200px; height: 1120px; overflow: hidden;
    background: var(--backdrop);
    font-family: "Roboto", Arial, sans-serif;
  }
  .sheet {
    width: 1200px; height: 1120px;
    display: flex; flex-direction: column; align-items: center; justify-content: center;
    gap: 60px;
  }
  .card {
    width: 840px; height: 480px;
    position: relative; overflow: hidden;
    box-shadow: 0 10px 30px rgba(0,0,0,.45);
  }

  /* Front: contact side */
  .card--front {
    background: var(--paper);
    display: flex; align-items: center;
    padding: 0 90px 0 110px;
  }
  .brand {
    display: flex; align-items: center; gap: 18px;
    width: 300px;
  }
  .brand__mark {
    width: 34px; height: 34px; background: var(--brand-blue); flex: none;
  }
  .brand__name {
    color: var(--brand-blue); font-weight: 700; text-transform: uppercase;
    font-size: 30px; line-height: 1.05; letter-spacing: .5px;
  }
  .brand__name span { display: block; font-size: 15.5px; letter-spacing: 1px; }
  .divider {
    width: 2px; height: 230px; background: var(--rule-grey); margin: 0 44px 0 20px;
  }
  .contact { color: var(--ink-grey); font-size: 17px; line-height: 1.35; }
  .contact__name {
    color: var(--brand-blue); font-weight: 700; font-size: 27px;
    text-transform: uppercase; letter-spacing: .3px;
  }
  .contact__role { margin-bottom: 22px; }
  .contact__address { margin-bottom: 22px; }
  .contact__line { display: flex; align-items: center; gap: 10px; }
  .contact__line svg { width: 14px; height: 14px; flex: none; }

  /* Back: brand side */
  .card--back {
    background: var(--brand-blue);
  }
  .back-brand {
    position: absolute; top: 70px; right: 70px;
    color: var(--paper); text-align: left; text-transform: uppercase; font-weight: 700;
  }
  .back-brand__name { font-size: 84px; line-height: 1; letter-spacing: 2px; }
  .back-brand__sub { font-size: 40px; font-weight: 400; letter-spacing: 1.5px; margin-top: 4px; }
</style>
</head>
<body>
<main class="sheet">
  <section class="card card--front" aria-label="Visitenkarte Vorderseite">
    <div class="brand">
      <div class="brand__mark"></div>
      <div class="brand__name">Kernwerk<span>Personalberatung</span></div>
    </div>
    <div class="divider"></div>
    <div class="contact">
      <p class="contact__name">Jonas Albrecht</p>
      <p class="contact__role">Geschäftsführer</p>
      <p class="contact__address">Lindenweg 12, 70180<br>Stuttgart, Germany</p>
      <p class="contact__line">
        <svg viewBox="0 0 14 14"><circle cx="7" cy="7" r="7" fill="#3a54a8"/><path d="M4.5 3.5l1.5 1.5-0.8 1a5 5 0 0 0 2.8 2.8l1-0.8 1.5 1.5-1 1C6.5 10.5 3.5 7.5 3.5 4.5z" fill="#fff"/></svg>
        +49 1520 4478210
      </p>
      <p class="contact__line">
        <svg viewBox="0 0 14 14"><circle cx="7" cy="7" r="7" fill="#3a54a8"/><rect x="3.5" y="4.5" width="7" height="5" fill="#fff"/><path d="M3.5 4.5L7 7.5l3.5-3" stroke="#3a54a8" fill="none" stroke-width="0.8"/></svg>
        kontakt@kernwerk-beratung.de
      </p>
      <p class="contact__line">
        <svg viewBox="0 0 14 14"><circle cx="7" cy="7" r="7" fill="#3a54a8"/><circle cx="7" cy="7" r="3.8" fill="none" stroke="#fff" stroke-width="0.9"/><path d="M3.2 7h7.6M7 3.2v7.6" stroke="#fff" stroke-width="0.9"/></svg>
        www.kernwerk-beratung.de
      </p>
    </div>
  </section>

  <section class="card card--back" aria-label="Visitenkarte Rückseite">
    <div class="back-brand">
      <p class="back-brand__name">Kernwerk</p>
      <p class="back-brand__sub">Personalberatung</p>
    </div>
  </section>
</main>
</body>
</html>
```